Website for Vornelix Capital, my new firm that raises money from investors to buy, build, own an...

Vornelix Capital needs a website! We are a new company with very experienced people, who invest in, own and build hotel properties, as well as apartments and other commercial real estate. We seek investors for our projects, and we provide safe, secure returns on their investment in our projects. Our new logo is designed to exhibit strength, class and security, and would like our website to continue on this theme. Our name, Vornelix, is a word-play on a Greek word “aristeia”, which means “excellence” and “a warriors finest moment of glory in war”. If you are in business, you realize that much of it is like war, with strategy and moves and opponents and competitors, and ever-changing economic conditions and threats that make business very much like war. We like to think that we are good at business (war), and so have named our company “Vornelix”, using the founders last name and the word “aristeia” combined. Another definition of "aristeia" is "performing at the peak of one's potential after a long struggle"...again, much like business in real life! The website design should exhibit financial security, smart moves, and positive growth towards a bright future.

Target Market(s)

The target market is smart and wealthy investors, with others such as brokers, cities and government agencies, lenders, sellers, partners, etc also looking at it.

Industry/Entity Type

Investment

Number of Pages Required

5+ page

Font styles to use
Sans Serif

Colors
fec214

Requirements
Must have
• Our website should have a landing page, a "about" or bio page, a projects page and a contact us page. Our new logo uses the colors black and gold, so this should be factored in to our site. The site should be simple, yet impactful and impressive. I have actually two logos, which can be mixed and interchanged in a complimentary way, each with their own unique look.
Nice to have
• I have uploaded a couple screenshots of a website i like, and the simplicity I mention.
Should not have
• The site should not be flashy or complicated or complex or "busy"

```html
<!DOCTYPE html>
<html lang="en">
<head>
<meta charset="utf-8">
<title>Vornelix Capital</title>
<link href="https://fonts.googleapis.com/css2?family=Montserrat:wght@400;500;600;700&family=Lato:ital,wght@0,400;0,700;1,700&display=swap" rel="stylesheet">
<style>
:root{
  --gold:#c9992b;
  --gold-light:#e0b448;
  --ink:#222222;
  --text:#555555;
  --white:#ffffff;
  --grey-mid:#555555;
  --grey-dark:#333333;
  --light:#efefef;
  --footer:#262626;
}
*{margin:0;padding:0;box-sizing:border-box}
html,body{width:1200px;height:4225px;overflow:hidden}
body{position:relative;background:var(--white);font-family:'Lato',sans-serif;color:var(--text)}
.abs{position:absolute}
.photo{position:absolute}
h1,h2,h3,.btn,.nav a,.brand{font-family:'Montserrat',sans-serif}
.btn{position:absolute;display:flex;align-items:center;justify-content:center;background:var(--gold);color:var(--white);font-weight:600;border-radius:40px;box-shadow:0 4px 0 #8f6a16;text-transform:uppercase}
.body-copy{font-size:15px;line-height:25px;color:var(--text)}

/* hero */
.hero{position:absolute;left:0;top:0;width:1200px;height:676px;background:linear-gradient(135deg,#5b6570,#3c4650 45%,#6b7078 70%,#8a8c8e)}
.hero-shade{position:absolute;inset:0;background:rgba(20,22,26,.35)}
.header{position:absolute;left:79px;top:42px;width:1042px;height:127px;background:var(--white)}
.brand-box{position:absolute;left:12px;top:8px;width:120px;height:110px;border:2px solid var(--ink);display:flex;align-items:center;justify-content:center}
.brand{font-size:17px;font-weight:700;color:var(--ink);letter-spacing:1px}
.nav{position:absolute;left:180px;top:50px;display:flex;gap:44px}
.nav a{font-size:15px;font-weight:500;color:#444;text-decoration:none;text-transform:uppercase;position:relative}
.nav a.active{color:var(--gold)}
.nav a.active::after{content:"";position:absolute;left:-4px;right:-4px;top:46px;height:5px;background:var(--gold)}
.phone-pill{position:absolute;left:642px;top:38px;width:226px;height:50px;border-radius:25px;background:var(--gold);color:var(--white);font-size:17px;font-weight:600;display:flex;align-items:center;padding-left:62px;font-family:'Montserrat',sans-serif}
.phone-pill .ic{position:absolute;left:4px;top:4px;width:42px;height:42px;border-radius:50%;background:var(--white);display:flex;align-items:center;justify-content:center}
.social{position:absolute;display:flex;gap:12px}
.social span{width:34px;height:34px;border-radius:50%;border:1px solid #bbb;display:block}
.hero-title{position:absolute;left:0;width:1200px;top:285px;text-align:center;font-family:'Montserrat',sans-serif;font-size:84px;font-weight:500;letter-spacing:10px;color:var(--white);text-shadow:0 0 1px var(--gold)}
.hero-sub{position:absolute;left:250px;width:700px;top:384px;text-align:center;color:var(--white);font-style:italic;font-weight:700;font-size:16px;line-height:28px}
.arrow{position:absolute;top:396px}
.thumb{position:absolute;top:628px;width:96px;height:96px;border-radius:50%;border:6px solid var(--white);box-shadow:0 2px 6px rgba(0,0,0,.3)}

/* about */
.spec-box{position:absolute;left:79px;top:794px;width:436px;height:333px;background:var(--gold)}
.spec-label{position:absolute;left:82px;top:960px;transform:translate(-50%,-50%) rotate(-90deg);transform-origin:center;color:var(--white);font-family:'Montserrat',sans-serif;font-weight:500;font-size:24px;letter-spacing:2px;white-space:nowrap;margin-left:26px}
h2.section{font-size:38px;font-weight:600;color:var(--ink);letter-spacing:1px}

/* services */
.service{position:absolute;top:1189px;width:400px;height:197px;color:var(--white)}
.service h3{position:absolute;left:106px;top:40px;font-size:22px;font-weight:500}
.service p{position:absolute;left:106px;top:80px;width:260px;font-size:14px;line-height:22px}
.service .ico{position:absolute;left:32px;top:38px}
.service .btn{left:243px;top:142px;width:120px;height:40px;font-size:13px}

/* projects */
.overlay{position:absolute;left:79px;top:1648px;width:470px;height:450px;background:rgba(201,153,43,.82);color:var(--white);text-align:center}
.overlay h3{margin-top:212px;font-size:22px;font-weight:500}
.overlay p{margin:12px auto 0;width:300px;font-size:15px;line-height:24px}

/* testimonial */
.testimonial{position:absolute;left:0;top:2746px;width:1200px;height:415px;background:var(--light)}
.quote-mark{position:absolute;left:175px;top:2790px;font-family:'Montserrat',sans-serif;font-weight:700;font-size:110px;line-height:1;color:var(--ink)}
.dots{position:absolute;left:79px;top:3084px;display:flex;gap:9px}
.dots span{width:12px;height:12px;border-radius:50%;border:1px solid #888}
.dots span.on{background:var(--gold);border-color:var(--gold)}

/* blog */
.date-col{position:absolute;width:84px}
.date-col div{display:flex;flex-direction:column;align-items:center;justify-content:center;color:var(--white);font-size:11px;text-align:center}
.blog-title{position:absolute;font-family:'Montserrat',sans-serif;font-size:19px;font-weight:500;color:var(--gold)}

/* footer */
.footer{position:absolute;left:0;top:3808px;width:1200px;height:333px;background:var(--footer);color:#ddd}
.footer h4{position:absolute;top:62px;font-family:'Montserrat',sans-serif;font-size:17px;font-weight:600;color:var(--gold);letter-spacing:1px;text-transform:uppercase}
.footer ul{position:absolute;list-style:none;font-size:15px;line-height:34px}
.copyright-bar{position:absolute;left:0;top:4141px;width:1200px;height:84px;background:var(--gold)}
</style>
</head>
<body>

<!-- Hero -->
<section class="hero">
  <div class="photo" role="img" aria-label="Two businessmen shaking hands in front of a city skyline" style="inset:0;background:linear-gradient(135deg,#5b6570,#3c4650 45%,#6b7078 70%,#8a8c8e)"></div>
  <div class="hero-shade"></div>

  <header class="header">
    <div class="brand-box"><span class="brand">VORNELIX</span></div>
    <nav class="nav">
      <a class="active" href="#">Home</a>
      <a href="#">About</a>
      <a href="#">Projects</a>
      <a href="#">Contact</a>
    </nav>
    <div class="phone-pill">
      <span class="ic"><svg width="20" height="20" viewBox="0 0 24 24"><path fill="#222" d="M6.6 10.8a15.1 15.1 0 0 0 6.6 6.6l2.2-2.2c.3-.3.7-.4 1-.2 1.1.4 2.3.6 3.6.6.6 0 1 .4 1 1V20c0 .6-.4 1-1 1A17 17 0 0 1 3 4c0-.6.4-1 1-1h3.5c.6 0 1 .4 1 1 0 1.3.2 2.5.6 3.6.1.3 0 .7-.2 1z"/></svg></span>
      +1 555 014 2290
    </div>
    <div class="social" style="left:888px;top:46px"><span></span><span></span><span></span></div>
  </header>

  <h1 class="hero-title">VORNELIX</h1>
  <p class="hero-sub">Lorem Ipsum is simply dummy text of the printing and typesetting industry. Lorem Ipsum has been the industry's standard dummy text ever since the 1500s.</p>
  <a class="btn" style="left:496px;top:468px;width:208px;height:64px;font-size:20px;font-weight:500">Contact Us</a>

  <svg class="arrow" style="left:78px" width="44" height="24" viewBox="0 0 44 24"><path d="M43 12H3M12 3 3 12l9 9" stroke="#fff" stroke-width="2" fill="none"/></svg>
  <svg class="arrow" style="left:1078px" width="44" height="24" viewBox="0 0 44 24"><path d="M1 12h40M32 3l9 9-9 9" stroke="#fff" stroke-width="2" fill="none"/></svg>
</section>
<div class="thumb" role="img" aria-label="Slide thumbnail: handshake" style="left:440px;background:linear-gradient(135deg,#6a5a48,#b89a6a)"></div>
<div class="thumb" role="img" aria-label="Slide thumbnail: business team" style="left:553px;background:linear-gradient(135deg,#8a7a60,#d0b78a)"></div>
<div class="thumb" role="img" aria-label="Slide thumbnail: meeting" style="left:666px;background:linear-gradient(135deg,#5a6878,#b8c2cc)"></div>

<!-- About -->
<section>
  <div class="spec-box"></div>
  <div class="spec-label">OUR SPECIALIZATION</div>
  <div class="photo" role="img" aria-label="Business colleagues reviewing a tablet in an office" style="left:146px;top:817px;width:446px;height:287px;background:linear-gradient(135deg,#dfe4ea,#8c9aa8 50%,#c8ced6)"></div>
  <h2 class="section abs" style="left:648px;top:788px">ABOUT US</h2>
  <p class="body-copy abs" style="left:648px;top:848px;width:470px">Lorem Ipsum is simply dummy text of the printing and typesetting industry. Lorem Ipsum has been the industry's standard dummy text ever since the 1500s, when an unknown printer took a galley of type and scrambled it to make a type specimen book. It has survived not only five centuries, but also the leap into electronic typesetting, remaining essentially unchanged. It was popularised in the 1960s with the release of Letraset sheets containing Lorem Ipsum passages.</p>
  <a class="btn" style="left:645px;top:1065px;width:166px;height:60px;font-size:17px;font-weight:500">Read More</a>
</section>

<!-- Services -->
<section>
  <div class="service" style="left:0;background:var(--grey-mid)">
    <svg class="ico" width="56" height="56" viewBox="0 0 56 56" fill="none" stroke="#fff" stroke-width="2"><rect x="8" y="14" width="40" height="38"/><path d="M4 14h48M18 4h20v10"/><path d="M15 22h6M26 22h6M37 22h4M15 31h6M26 31h6M37 31h4M15 40h6M37 40h4M25 52V41h7v11"/></svg>
    <h3>Build Hotel Properties</h3>
    <p>Lorem Ipsum is simply dummy text of the printing and typesetting industry.</p>
    <a class="btn">Read More</a>
  </div>
  <div class="service" style="left:400px;background:var(--grey-dark)">
    <svg class="ico" width="56" height="56" viewBox="0 0 56 56" fill="none" stroke="#fff" stroke-width="2"><rect x="6" y="10" width="24" height="42"/><rect x="30" y="24" width="20" height="28"/><path d="M12 18h4M20 18h4M12 27h4M20 27h4M12 36h4M20 36h4M36 32h8M36 40h8"/></svg>
    <h3>Build Apartments</h3>
    <p>Lorem Ipsum is simply dummy text of the printing and typesetting industry.</p>
    <a class="btn">Read More</a>
  </div>
  <div class="service" style="left:800px;width:400px;background:var(--grey-mid)">
    <svg class="ico" width="56" height="56" viewBox="0 0 56 56" fill="none" stroke="#fff" stroke-width="2"><path d="M4 26 28 6l24 20M10 22v30h36V22"/><rect x="22" y="34" width="12" height="18"/><rect x="14" y="28" width="6" height="6"/></svg>
    <h3>Commercial Real Estate</h3>
    <p>Lorem Ipsum is simply dummy text of the printing and typesetting industry.</p>
    <a class="btn">Read More</a>
  </div>
</section>

<!-- Projects -->
<section>
  <h2 class="section abs" style="left:79px;top:1487px">OUR PROJECTS</h2>
  <p class="body-copy abs" style="left:79px;top:1550px;width:600px">Lorem Ipsum is simply dummy text of the printing and typesetting industry. Lorem Ipsum has been the industry's standard dummy text ever since the 1500s.</p>

  <div class="photo" role="img" aria-label="Business partners in discussion" style="left:79px;top:1628px;width:510px;height:513px;background:linear-gradient(135deg,#b7bec6,#e6e8ea 50%,#8f98a2)"></div>
  <div class="overlay"><h3>LOREM IPSUM</h3><p>Lorem Ipsum is simply dummy text of the printing and typesetting industry.</p></div>

  <div class="photo" role="img" aria-label="Team working at a laptop" style="left:614px;top:1628px;width:240px;height:240px;background:linear-gradient(135deg,#c9ccd0,#7c8590)"></div>
  <div class="photo" role="img" aria-label="Colleagues at a desk with laptop" style="left:882px;top:1628px;width:239px;height:240px;background:linear-gradient(135deg,#dadde0,#8a96a2)"></div>
  <div class="photo" role="img" aria-label="Overhead view of a team around a table" style="left:614px;top:1893px;width:507px;height:248px;background:linear-gradient(135deg,#c2b8a8,#857a6c 50%,#d4ccc0)"></div>
  <div class="photo" role="img" aria-label="Businessmen reviewing documents" style="left:79px;top:2163px;width:239px;height:243px;background:linear-gradient(135deg,#e2e4e6,#9aa2aa)"></div>
  <div class="photo" role="img" aria-label="Smiling businessman in an office" style="left:346px;top:2163px;width:243px;height:243px;background:linear-gradient(135deg,#7c8794,#c4cad0)"></div>
  <div class="photo" role="img" aria-label="Hands pointing at financial charts beside a laptop" style="left:79px;top:2431px;width:510px;height:245px;background:linear-gradient(135deg,#dfe6ee,#8ea2b6)"></div>
  <div class="photo" role="img" aria-label="Team meeting around a conference table" style="left:614px;top:2163px;width:507px;height:513px;background:linear-gradient(135deg,#a8b2bc,#4e5a66 50%,#9aa4ae)"></div>
</section>

<!-- Testimonial -->
<section class="testimonial">
  <div class="photo" role="img" aria-label="Smiling couple portrait" style="left:493px;top:0;width:707px;height:415px;background:linear-gradient(90deg,rgba(239,239,239,0),#d8cfc6 25%,#b9c8d2 70%,#e6ecf0)"></div>
</section>
<div class="quote-mark">&ldquo;</div>
<h2 class="abs" style="left:79px;top:2873px;font-size:38px;font-weight:600;color:var(--gold);letter-spacing:1px">TESTIMONIAL</h2>
<p class="body-copy abs" style="left:79px;top:2935px;width:580px">Lorem Ipsum is simply dummy text of the printing and typesetting industry. Lorem Ipsum has been the industry's standard dummy text and scrambled it to make a type specimen book.</p>
<p class="abs" style="left:79px;top:3030px;font-size:18px;font-weight:700;color:var(--ink)">- M. KASTOR</p>
<div class="dots"><span></span><span></span><span></span><span class="on"></span></div>

<!-- Blog -->
<section>
  <h2 class="section abs" style="left:0;width:1200px;text-align:center;top:3216px">RECENT BLOG</h2>

  <div class="photo" role="img" aria-label="City skyline at sunset" style="left:163px;top:3296px;width:421px;height:253px;background:linear-gradient(180deg,#6fa6d6,#c7a57c 60%,#6a6258)"></div>
  <div class="date-col" style="left:79px;top:3296px">
    <div style="height:82px;background:var(--gold)"><b style="font-size:26px;font-family:'Montserrat',sans-serif">26</b>Sept - 2018</div>
    <div style="height:84px;background:#2e2e2e;border-top:2px solid #fff">
      <svg width="24" height="24" viewBox="0 0 24 24"><path d="M4 4h16v12H9l-5 4z" fill="none" stroke="#fff" stroke-width="2"/></svg>10 - Comm</div>
    <div style="height:87px;background:#2e2e2e;border-top:2px solid #fff">
      <svg width="26" height="18" viewBox="0 0 26 18"><path d="M1 9s5-8 12-8 12 8 12 8-5 8-12 8S1 9 1 9z" fill="none" stroke="#fff" stroke-width="2"/><circle cx="13" cy="9" r="3" fill="#fff"/></svg>401<br>View</div>
  </div>
  <p class="blog-title" style="left:170px;top:3570px">Lorem printing and typesetting industry.</p>
  <p class="body-copy abs" style="left:170px;top:3606px;width:400px">Lorem Ipsum is simply dummy text of the printing and typesetting industry. Lorem Ipsum has been the industry's specimen book.</p>
  <a class="btn" style="left:166px;top:3699px;width:124px;height:42px;font-size:14px">Read More</a>

  <div class="photo" role="img" aria-label="Modern apartment building under blue sky" style="left:704px;top:3296px;width:417px;height:253px;background:linear-gradient(180deg,#3f7fc8,#9cc0e4 55%,#5a6470)"></div>
  <div class="date-col" style="left:620px;top:3296px">
    <div style="height:82px;background:var(--gold)"><b style="font-size:26px;font-family:'Montserrat',sans-serif">26</b>Sept - 2018</div>
    <div style="height:84px;background:#2e2e2e;border-top:2px solid #fff">
      <svg width="24" height="24" viewBox="0 0 24 24"><path d="M4 4h16v12H9l-5 4z" fill="none" stroke="#fff" stroke-width="2"/></svg>10 - Comm</div>
    <div style="height:87px;background:#2e2e2e;border-top:2px solid #fff">
      <svg width="26" height="18" viewBox="0 0 26 18"><path d="M1 9s5-8 12-8 12 8 12 8-5 8-12 8S1 9 1 9z" fill="none" stroke="#fff" stroke-width="2"/><circle cx="13" cy="9" r="3" fill="#fff"/></svg>401<br>View</div>
  </div>
  <p class="blog-title" style="left:708px;top:3570px">Lorem printing and typesetting industry.</p>
  <p class="body-copy abs" style="left:708px;top:3606px;width:400px">Lorem Ipsum is simply dummy text of the printing and typesetting industry. Lorem Ipsum has been the industry's specimen book.</p>
  <a class="btn" style="left:704px;top:3699px;width:124px;height:42px;font-size:14px">Read More</a>
</section>

<!-- Footer -->
<footer class="footer">
  <div class="abs" style="left:135px;top:50px;width:130px;height:130px;border:2px solid var(--gold);display:flex;align-items:center;justify-content:center"><span class="brand" style="color:var(--white)">VORNELIX</span></div>
  <p class="abs" style="left:79px;top:196px;width:300px;font-size:15px;line-height:25px">Lorem Ipsum is simply dummy the text of the printing and Printing of <u>READ MORE</u></p>

  <h4 style="left:399px">Useful Links</h4>
  <ul style="left:412px;top:100px"><li style="color:var(--gold)">- Home</li><li>- About</li><li>- Projects</li><li>- Contact</li></ul>

  <h4 style="left:605px">Get In Touch</h4>
  <div class="abs" style="left:605px;top:104px;font-size:15px;line-height:26px">
    <p style="display:flex;gap:14px;align-items:center"><svg width="18" height="18" viewBox="0 0 24 24"><path fill="#fff" d="M6.6 10.8a15.1 15.1 0 0 0 6.6 6.6l2.2-2.2c.3-.3.7-.4 1-.2 1.1.4 2.3.6 3.6.6.6 0 1 .4 1 1V20c0 .6-.4 1-1 1A17 17 0 0 1 3 4c0-.6.4-1 1-1h3.5c.6 0 1 .4 1 1 0 1.3.2 2.5.6 3.6.1.3 0 .7-.2 1z"/></svg>+1 555 014 2290</p>
    <p style="display:flex;gap:14px;align-items:center;margin-top:26px"><svg width="18" height="14" viewBox="0 0 24 18"><rect width="24" height="18" fill="#fff"/><path d="M1 1l11 9 11-9" stroke="#262626" stroke-width="2" fill="none"/></svg>info@vornelixcapital.com</p>
    <p style="display:flex;gap:14px;align-items:flex-start;margin-top:26px"><svg width="18" height="22" viewBox="0 0 24 30"><path fill="#fff" d="M12 0a10 10 0 0 0-10 10c0 8 10 20 10 20s10-12 10-20A10 10 0 0 0 12 0zm0 14a4 4 0 1 1 0-8 4 4 0 0 1 0 8z"/></svg><span>123, Address, State Name<br>City, Street, Zipcode</span></p>
  </div>

  <h4 style="left:874px">Subscribe Newsletter</h4>
  <p class="abs" style="left:874px;top:100px;width:250px;font-size:15px;line-height:25px">Would you like to receive exclusive access to articles, white papers and our regular monthly newsletter?</p>
  <div class="abs" style="left:874px;top:208px;width:250px;height:46px;border-radius:23px;background:var(--white);overflow:hidden">
    <span class="abs" style="left:20px;top:13px;font-size:14px;color:#555">Email</span>
    <div class="abs" style="right:0;top:0;width:62px;height:46px;background:var(--gold);display:flex;align-items:center;justify-content:center">
      <svg width="22" height="22" viewBox="0 0 24 24"><path fill="#fff" d="M2 11 22 2l-7 20-4-8z"/></svg>
    </div>
  </div>
</footer>
<div class="copyright-bar">
  <p class="abs" style="left:79px;top:32px;font-size:13px;color:var(--white)">Copyright © <b>VORNELIX CAPITAL</b> - 2018. All Right Reserved</p>
  <div class="social" style="left:946px;top:18px;gap:20px">
    <span style="width:50px;height:50px;background:var(--white);border:none"></span>
    <span style="width:50px;height:50px;background:var(--white);border:none"></span>
    <span style="width:50px;height:50px;background:var(--white);border:none"></span>
  </div>
</div>

</body>
</html>
```